Letter and Envelope Design For Harborline Realty

Please design a letter and an envelope incorporating our logo (See Attached). We are also launched a business card contest. Since we want them to match, please feel free to submit a design for both the business card and also the letter design and envelope.

Requirements
Must have
• The envelope, the letter and the business cards must match somehow connecting the designs. We want them to have something that holds them together besides the logo.

```html
<!DOCTYPE html>
<html lang="en">
<head>
<meta charset="utf-8">
<title>Harborline Realty Stationery</title>
<link href="https://fonts.googleapis.com/css2?family=Montserrat:wght@500;600;700&family=Source+Sans+3:wght@400;600;700&display=swap" rel="stylesheet">
<style>
:root{
  --blue:#0a1a8c;
  --blue-soft:#2a3aa6;
  --grey:#58595b;
  --ink:#3a3a3c;
  --paper:#ffffff;
  --backdrop:#e7e8ea;
}
*{box-sizing:border-box;margin:0;padding:0}
html,body{width:1200px;height:825px;overflow:hidden;background:var(--backdrop)}
body{position:relative;font-family:"Source Sans 3",sans-serif;color:var(--ink)}
.sheet{position:absolute;background:var(--paper);overflow:hidden}

.footer-band{position:absolute;left:0;bottom:0;width:100%;background:linear-gradient(180deg,var(--blue-soft) 0%,var(--blue) 55%)}

.brand{position:absolute;display:flex;align-items:center;gap:6px;font-family:"Montserrat",sans-serif;font-weight:600;color:var(--blue);letter-spacing:1.6px;line-height:1.15;text-transform:uppercase;white-space:nowrap}
.brand-dot{border:2px solid var(--blue);border-radius:50%;flex:none}
.brand.light{color:#fff}
.brand.light .brand-dot{border-color:#fff}

.contact{position:absolute;list-style:none;font-size:8px;line-height:9px;color:var(--ink);white-space:nowrap}
.contact li{display:flex;align-items:center;gap:3px}
.contact svg{width:6px;height:6px;fill:var(--blue)}

/* Letter */
.letter{left:80px;top:82px;width:466px;height:659px}
.letter .brand{left:36px;top:44px;font-size:11px}
.letter .brand-dot{width:26px;height:26px}
.letter .contact{left:338px;top:47px}
.salutation{position:absolute;left:38px;top:126px;font-weight:700;font-size:11.5px;color:#1d1d1f}
.body-copy{position:absolute;left:38px;top:152px;width:390px;font-size:9.6px;line-height:12.2px;text-align:justify;color:#4a4a4c}
.body-copy p{margin-bottom:12.2px}
.signature{position:absolute;left:37px;top:472px;width:72px;height:34px;background:#ececee;border-radius:4px}
.letter .footer-band{height:74px}
.letter-footer{position:absolute;left:38px;bottom:14px;color:#fff;font-size:7.6px;line-height:9.6px}
.letter-footer strong{font-weight:700;display:block}

/* Business cards */
.card-front{left:646px;top:103px;width:196px;height:112px}
.card-front .brand{left:13px;top:16px;font-size:7px;letter-spacing:1px}
.card-front .brand-dot{width:18px;height:18px;border-width:1.5px}
.person{position:absolute;right:10px;top:37px;text-align:right}
.person .name{font-family:"Montserrat",sans-serif;font-weight:700;font-size:6.4px;color:var(--blue)}
.person .role{font-size:6px;color:#888}
.card-front .contact{right:10px;top:66px;font-size:5.2px;line-height:7px;text-align:right}
.card-front .contact li{justify-content:flex-end}
.card-front .contact svg{width:4px;height:4px}
.card-front .footer-band{height:24px}
.card-address{position:absolute;left:12px;bottom:4px;color:#fff;font-size:5px;line-height:7px}
.card-back{left:862px;top:103px;width:196px;height:112px;background:var(--blue)}
.card-back .brand{left:50%;top:50%;transform:translate(-50%,-50%);font-size:9px}
.card-back .brand-dot{width:22px;height:22px}

/* Compliment slip */
.slip{left:585px;top:240px;width:534px;height:231px}
.slip .brand{left:30px;top:34px;font-size:11.5px}
.slip .brand-dot{width:30px;height:30px}
.slip .contact{left:401px;top:35px}
.slip .footer-band{height:70px}

/* Envelope */
.envelope{left:585px;top:510px;width:534px;height:232px}
.flap{position:absolute;left:0;top:0;width:100%;height:56px;display:block}
.envelope .brand{left:50%;top:16px;transform:translateX(-50%);font-size:10px}
.envelope .brand-dot{width:20px;height:20px}
</style>
</head>
<body>

<svg width="0" height="0" style="position:absolute" aria-hidden="true">
  <defs>
    <symbol id="i-phone" viewBox="0 0 10 10"><path d="M2 0h2l1 3-1.5 1a6 6 0 0 0 2.5 2.5L7 5l3 1v2a2 2 0 0 1-2 2A8 8 0 0 1 0 2a2 2 0 0 1 2-2z"/></symbol>
    <symbol id="i-mail" viewBox="0 0 10 10"><path d="M0 2h10v6H0z"/></symbol>
    <symbol id="i-web" viewBox="0 0 10 10"><circle cx="5" cy="5" r="5"/></symbol>
  </defs>
</svg>

<section class="sheet letter">
  <div class="brand"><span class="brand-dot"></span><span>Harborline<br>Realty</span></div>
  <ul class="contact">
    <li><svg><use href="#i-phone"/></svg>555-014-2290</li>
    <li><svg><use href="#i-mail"/></svg>info@harborlinerealty.com</li>
    <li><svg><use href="#i-web"/></svg>info@harborlinerealty.com</li>
  </ul>
  <p class="salutation">Dear Mr. Ellis,</p>
  <div class="body-copy">
    <p>Lorem Ipsum is simply dummy text of the printing and typesetting industry. Lorem Ipsum has been the industry's standard dummy text ever since the 1500s, when an unknown printer took a galley of type and scrambled it to make a type specimen book. It has survived not only five centuries, but also the leap into electronic typesetting, remaining essentially unchanged.</p>
    <p>The standard chunk of Lorem Ipsum used since the 1500s is reproduced below for those interested. Sections 1.10.32 and 1.10.33 from "de Finibus Bonorum et Malorum" by Cicero are also reproduced in their exact original form, accompanied by English versions from the 1914 translation by H. Rackham</p>
    <p>Lorem Ipsum is simply dummy text of the printing and typesetting industry. Lorem Ipsum has been the industry's standard dummy text ever since the 1500s, when an unknown printer took a galley of type and scrambled it to make a type specimen book. It has survived not only five centuries, but also the leap into electronic typesetting, remaining essentially unchanged. It was popularised in the</p>
    <p>The standard chunk of Lorem Ipsum used since the 1500s is reproduced below for those interested. Sections 1.10.32 and 1.10.33 from "de Finibus Bonorum et Malorum" by Cicero are also reproduced in their exact original form, accompanied by English versions from the 1914 translation by H. Rackham</p>
    <p>The standard chunk of Lorem Ipsum used since the 1500s is reproduced below for those interested. Sections 1.10.32 and 1.10.33 from "de Finibus Bonorum et Malorum" by Cicero are also reproduced in their exact original form.</p>
  </div>
  <div class="signature" role="img" aria-label="Handwritten signature of the sender"></div>
  <div class="footer-band" role="img" aria-label="Blue decorative footer band"></div>
  <div class="letter-footer"><strong>Harborline Realty</strong>Po. box 201, Street Name, City Name, Zip Code - 00000</div>
</section>

<section class="sheet card-front">
  <div class="brand"><span class="brand-dot"></span><span>Harborline<br>Realty</span></div>
  <div class="person"><div class="name">DANA WHITLOW</div><div class="role">Project Manager</div></div>
  <ul class="contact">
    <li>555-014-2290<svg><use href="#i-phone"/></svg></li>
    <li>info@harborlinerealty.com<svg><use href="#i-mail"/></svg></li>
    <li>www.harborlinerealty.com<svg><use href="#i-web"/></svg></li>
  </ul>
  <div class="footer-band" role="img" aria-label="Blue decorative footer band"></div>
  <div class="card-address">Po. box 201, Street Name,<br>City Name, Zip Code - 00000</div>
</section>

<section class="sheet card-back">
  <div class="brand light"><span class="brand-dot"></span><span>Harborline<br>Realty</span></div>
</section>

<section class="sheet slip">
  <div class="brand"><span class="brand-dot"></span><span>Harborline<br>Realty</span></div>
  <ul class="contact">
    <li><svg><use href="#i-phone"/></svg>555-014-2290</li>
    <li><svg><use href="#i-mail"/></svg>info@harborlinerealty.com</li>
    <li><svg><use href="#i-web"/></svg>info@harborlinerealty.com</li>
  </ul>
  <div class="footer-band" role="img" aria-label="Blue decorative footer band"></div>
</section>

<section class="sheet envelope">
  <svg class="flap" viewBox="0 0 534 56" preserveAspectRatio="none" aria-hidden="true">
    <path d="M0,0 H534 L531,36 Q530,44 518,45 Q400,52 267,54 Q134,52 16,45 Q4,44 3,36 Z" fill="#0a1a8c"/>
  </svg>
  <div class="brand light"><span class="brand-dot"></span><span>Harborline Realty</span></div>
</section>

</body>
</html>
```